Chimney Service company needs new business card design

We need a updated business card with our new logo added. We provide a full range of chimney services throughout Vermont and New Hampshire. The business card will be one sided and color. Attached is our current business card another document showing all the information we would like on the card.
We dont like a lot of flashy colors.... here is a link to our website to get an idea of our branding www.flueguardianvt.example

Target Market(s)

homeowners

Industry/Entity Type

Business

Contact Information for Business Card

See attached sheet for content.

Font styles to use
Serif
Sans Serif

Requirements
Must have
• all information provided on separate sheet
Should not have
• Additional information that may clogg up design

```html
<!DOCTYPE html>
<html lang="en">
<head>
<meta charset="utf-8">
<title>Flue Guardian — Business Card</title>
<link rel="stylesheet" href="https://fonts.googleapis.com/css2?family=Cinzel:wght@400;700&family=Lato:ital,wght@0,400;1,400&display=swap">
<style>
  :root {
    --page-bg: #e4ddd4;
    --card-bg: #f4f1ec;
    --ink: #2f2c2a;
    --ink-soft: #4a4643;
    --brand-red: #9b1c22;
    --band-red: #8e1a1f;
    --band-text: #efe3dc;
  }
  * { margin: 0; padding: 0; box-sizing: border-box; }
  html, body {
    width: 1200px; height: 1047px; overflow: hidden;
    background: var(--page-bg);
  }
  .card {
    position: absolute; left: 80px; top: 236px;
    width: 1040px; height: 574px;
    background: var(--card-bg);
    border-radius: 22px;
    overflow: hidden;
    box-shadow: 0 10px 30px rgba(60, 45, 35, 0.18);
    font-family: 'Lato', sans-serif;
    color: var(--ink);
  }
  .brand-mark {
    position: absolute; left: 206px; top: 121px;
    width: 160px; height: 160px;
    border: 12px solid var(--ink-soft);
  }
  .brand-name {
    position: absolute; left: 40px; top: 305px; width: 470px;
    text-align: center;
    font-family: 'Cinzel', serif; font-weight: 400;
    font-size: 40px; letter-spacing: 1px;
    color: var(--ink-soft);
  }
  .divider {
    position: absolute; left: 539px; top: 89px;
    width: 3px; height: 310px; background: var(--brand-red);
  }
  .contact {
    position: absolute; left: 584px; top: 90px; list-style: none;
  }
  .contact li {
    display: flex; align-items: center; height: 32px;
    font-size: 21px; letter-spacing: 0.4px;
  }
  .contact svg { width: 18px; height: 18px; margin-right: 25px; fill: var(--brand-red); }
  .services { position: absolute; left: 627px; top: 208px; }
  .services h2 {
    font-family: 'Cinzel', serif; font-weight: 700;
    font-size: 28px; color: var(--brand-red); letter-spacing: 0.5px;
    margin-bottom: 4px;
  }
  .services ul { list-style: none; }
  .services li { font-size: 21px; line-height: 32px; }
  .tagline {
    position: absolute; left: 0; right: 0; top: 458px;
    text-align: center;
    font-family: 'Cinzel', serif; font-size: 22px; color: var(--ink-soft);
  }
  .tagline em {
    font-family: 'Lato', sans-serif; font-style: italic;
    color: var(--brand-red); font-size: 23px;
  }
  .promise-band {
    position: absolute; left: 0; right: 0; bottom: 0; height: 64px;
    background: linear-gradient(180deg, #a3222a, var(--band-red));
    display: flex; align-items: center; justify-content: center;
    font-family: 'Cinzel', serif; font-size: 23px;
    color: var(--band-text); letter-spacing: 0.5px;
  }
</style>
</head>
<body>
  <article class="card">
    <div class="brand-mark"></div>
    <h1 class="brand-name">FLUE GUARDIAN</h1>

    <div class="divider"></div>

    <ul class="contact">
      <li>
        <svg viewBox="0 0 24 24"><path d="M6.6 10.8a15.1 15.1 0 0 0 6.6 6.6l2.2-2.2c.3-.3.7-.4 1-.2 1.1.4 2.3.6 3.6.6.6 0 1 .4 1 1V20c0 .6-.4 1-1 1A17 17 0 0 1 3 4c0-.6.4-1 1-1h3.5c.6 0 1 .4 1 1 0 1.3.2 2.5.6 3.6.1.3 0 .7-.2 1z"/></svg>
        802-555-0147
      </li>
      <li>
        <svg viewBox="0 0 24 24"><path d="M2 5h20v14H2z" /><path d="M2 5l10 7 10-7" fill="none" stroke="#f4f1ec" stroke-width="2"/></svg>
        info@flueguardianvt.example
      </li>
      <li>
        <svg viewBox="0 0 24 24"><circle cx="12" cy="12" r="9" fill="none" stroke="#9b1c22" stroke-width="2"/><path d="M3 12h18M12 3c3 3 3 15 0 18M12 3c-3 3-3 15 0 18" fill="none" stroke="#9b1c22" stroke-width="1.6"/></svg>
        www.flueguardianvt.example
      </li>
    </ul>

    <section class="services">
      <h2>SERVICES WE PROVIDE</h2>
      <ul>
        <li>Full Masonry Services</li>
        <li>Historic chimney restoration</li>
        <li>Stainless steel liners</li>
        <li>New Chimney installations</li>
        <li>Hearthline Certified Chimney sweeps</li>
      </ul>
    </section>

    <p class="tagline">SERVING VT AND NEW HAMPSHIRE-<em>since 1989</em></p>

    <div class="promise-band">Fully Insured–Free Estimates | Family owned and operated</div>
  </article>
</body>
</html>
```